Brand new letterhead, business card, email signature etc.

We are a financial company in London, UK. Our website is www.marlowvane.com. We're wanting a complete remodel of the company colours, letter head, business cards, email signatures, etc. Looking to keep the same font for the company name. I have upload a colour palette that we want to work with. We're looking for company letterhead for outgoing letters/ correspondence, letterhead for internal documentation, email signatures, e-letters. etc. Ultimately we will redesign the entire website also. It is important that our clients get a strong, secure, warm, trustworthy, solid feeling and first impression.
Updates

Designs look the same

Target Market(s)

Institutional investors, (ultra) high net worth individuals

Industry/Entity Type

Finance, Invesments banking.

Font styles to use
Other font styles liked:
• Current font is "Champagne & Limousines"

Requirements
Must have
• Must use the colours provided on the PDF uploaded to the portal. The purple = main colour. The red = accent colour.
Nice to have
• Nice to use same font as now for the company name "Corvane". Font is "Champagne & Limousines". Nice to have some reference to the old logo flower, but only subtle.
Should not have
• Do not use the colour red from our website. Use the colours provided on the colour palette PDF that I uploaded in the portal.

```html
<!DOCTYPE html>
<html lang="en">
<head>
<meta charset="utf-8">
<title>Corvane Letterhead</title>
<link rel="stylesheet" href="https://fonts.googleapis.com/css2?family=Open+Sans:wght@400;600;700&family=Josefin+Sans:wght@300&family=Raleway:wght@700&display=swap">
<style>
  :root {
    --backdrop: #d8d5d1;
    --paper: #e9e9e9;
    --accent-red: #d4524a;
    --main-purple: #473540;
    --ink-dark: #3e2f37;
    --ink-body: #8c8c8c;
    --ink-soft: #8a8a8a;
    --icon-fill: #ececec;
  }
  * { box-sizing: border-box; margin: 0; padding: 0; }
  html, body {
    width: 1200px; height: 1200px; overflow: hidden;
    background: var(--backdrop);
  }
  .letterhead {
    position: absolute; left: 166px; top: 40px;
    width: 868px; height: 1120px;
    background: var(--paper);
    box-shadow: 0 4px 18px rgba(0,0,0,0.18);
    font-family: "Open Sans", sans-serif;
  }
  .band-accent {
    position: absolute; left: 0; top: 0; width: 40px; height: 100%;
    background: var(--accent-red);
  }
  .band-main {
    position: absolute; left: 40px; top: 0; width: 20px; height: 100%;
    background: var(--main-purple);
  }
  .brand-name {
    position: absolute; left: 130px; top: 48px;
    font-family: "Open Sans", sans-serif; font-weight: 400;
    font-size: 30px; line-height: 40px; color: var(--ink-dark);
  }
  .sender {
    position: absolute; left: 130px; top: 222px;
  }
  .sender-name {
    font-weight: 700; font-size: 19.5px; color: var(--ink-dark);
    margin-bottom: 5px;
  }
  .sender-line {
    font-size: 13.2px; line-height: 18.5px; color: var(--ink-soft);
  }
  .letter-body {
    position: absolute; left: 130px; top: 366px; width: 657px;
    font-size: 13.1px; line-height: 18.4px; color: var(--ink-body);
    text-align: justify;
  }
  .letter-body p { margin-bottom: 18.4px; }
  .sign-off {
    position: absolute; right: 82px; top: 882px;
    text-align: right;
  }
  .signature-area {
    display: block; margin-left: auto;
    width: 154px; height: 28px;
    background: linear-gradient(90deg, rgba(62,47,55,0.25), rgba(62,47,55,0.45));
    border-radius: 4px;
    margin-bottom: 4px;
  }
  .signer-name {
    font-family: "Raleway", sans-serif; font-weight: 700;
    font-size: 17px; color: var(--ink-dark); letter-spacing: 0.3px;
  }
  .signer-role {
    font-size: 13px; color: var(--ink-soft); margin-top: 2px;
  }
  .contact-tab {
    position: absolute; left: 40px; top: 937px;
    width: 67px; height: 158px;
    background: var(--main-purple);
    border-radius: 0 8px 8px 0;
  }
  .contact-icon {
    position: absolute; left: 72px;
    width: 28px; height: 28px;
  }
  .contact-icon.home { top: 958px; }
  .contact-icon.send { top: 1002px; }
  .contact-icon.phone { top: 1045px; }
  .contact-list {
    position: absolute; left: 126px; top: 956px;
    font-family: "Josefin Sans", sans-serif; font-weight: 300;
    font-size: 12px; line-height: 15.5px; color: var(--ink-dark);
    font-style: normal;
  }
  .contact-group { margin-bottom: 12px; }
</style>
</head>
<body>
  <main class="letterhead">
    <div class="band-accent"></div>
    <div class="band-main"></div>

    <header class="brand-name">Corvane</header>

    <section class="sender">
      <div class="sender-name">Name Surname</div>
      <div class="sender-line">Senior Executive</div>
      <div class="sender-line">Address goes here. Street, City, Country</div>
      <div class="sender-line">contact@marlowvane.com</div>
      <div class="sender-line">+44 20 7946 0215</div>
    </section>

    <article class="letter-body">
      <p>Lorem ipsum dolor sit amet, consectetur adipisicing elit, sed do eiusmod tempor incididunt ut labore et dolore magna aliqua. Ut enim ad minim veniam, quis nostrud exercitation ullamco laboris nisi ut aliquip ex ea commodo consequat. Duis aute irure dolor in reprehenderit in voluptate velit esse cillum dolore eu fugiat nulla pariatur. Excepteur sint occaecat cupidatat non proident, sunt in culpa qui officia deserunt mollit anim id est laborum. Sed ut perspiciatis unde omnis iste natus error sit voluptatem accusantium doloremque laudantium, totam rem aperiam, eaque ipsa quae ab illo inventore veritatis et quasi architecto beatae vitae dicta sunt explicabo. Nemo enim ipsam voluptatem quia voluptas sit aspernatur aut odit aut fugit, sed quia consequuntur magni dolores eos qui ratione voluptatem sequi nesciunt. Neque porro voluptatem sequi nesciunt. Nemo enim ipsam voluptatem quia voluptas.</p>
      <p>Lorem ipsum dolor sit amet, consectetur adipisicing elit, sed do eiusmod tempor incididunt ut labore et dolore magna aliqua. Ut enim ad minim veniam, quis nostrud exercitation ullamco laboris nisi ut aliquip ex ea commodo consequat. Duis aute irure dolor in reprehenderit in voluptate velit esse cillum dolore eu fugiat nulla pariatur. Excepteur sint occaecat cupidatat non proident, sunt in culpa qui officia deserunt mollit anim id est laborum. Sed ut perspiciatis unde omnis iste natus error sit voluptatem accusantium doloremque laudantium, totam rem aperiam, eaque ipsa quae ab illo inventore veritatis et quasi architecto beatae vitae dicta sunt explicabo. Nemo enim ipsam voluptatem quia voluptas sit aspernatur aut odit aut.</p>
      <p>Lorem ipsum dolor sit amet, consectetur adipisicing elit, sed do eiusmod tempor incididunt ut labore et dolore magna aliqua. Ut enim ad minim veniam, quis nostrud exercitation ullamco laboris nisi ut aliquip ex ea commodo consequat.</p>
    </article>

    <section class="sign-off">
      <div class="signature-area" role="img" aria-label="Handwritten signature of the sender"></div>
      <div class="signer-name">NAME SURNAME</div>
      <div class="signer-role">General Manager</div>
    </section>

    <div class="contact-tab"></div>

    <svg class="contact-icon home" viewBox="0 0 28 28" aria-hidden="true">
      <circle cx="14" cy="14" r="14" fill="var(--icon-fill)"/>
      <path d="M14 6.5 L6 13.5 H8.5 V21 H12 V16.5 H16 V21 H19.5 V13.5 H22 Z" fill="var(--main-purple)"/>
    </svg>
    <svg class="contact-icon send" viewBox="0 0 28 28" aria-hidden="true">
      <circle cx="14" cy="14" r="14" fill="var(--icon-fill)"/>
      <path d="M7 9 L21 13 L12 15.5 L9.5 21 Z" fill="var(--main-purple)"/>
    </svg>
    <svg class="contact-icon phone" viewBox="0 0 28 28" aria-hidden="true">
      <circle cx="14" cy="14" r="14" fill="var(--icon-fill)"/>
      <path d="M7 11.5 Q14 6.5 21 11.5 L20 13.5 L17.5 13 L17 11.5 Q14 10.5 11 11.5 L10.5 13 L8 13.5 Z" fill="var(--main-purple)"/>
      <path d="M9.5 20.5 L11 14.5 H17 L18.5 20.5 Z" fill="var(--main-purple)"/>
      <circle cx="14" cy="17.3" r="1.6" fill="var(--icon-fill)"/>
    </svg>

    <address class="contact-list">
      <div class="contact-group">
        <div>Street Address Here</div>
        <div>Street Address Here</div>
      </div>
      <div class="contact-group">
        <div>office@marlowvane.com</div>
        <div>www.marlowvane.com</div>
      </div>
      <div class="contact-group">
        <div>+44 20 7946 0381</div>
        <div>+44 20 7946 0381</div>
      </div>
    </address>
  </main>
</body>
</html>
```